International Manufacturing Business Needs A Heavy Hitting Wordpress Design!

We need wordpress template designs for a new website for our UK based International company Dalvesham Engineering Ltd. We manufacture and supply steel security doors and window units. We would like designs that feature the black and yellow industrial "stripes" that can be seen at our current site www.dalvoportals.com. The final design should communicate strength, power and weight to represent the quality of the products and the security that they provide.

It feels like we need 3 different types of page to be able to be created as per the current website at www.dalvosafeportals.com.

Homepage
Products/Accessories
Leadtimes/Downloads/Contact

It may be that 3 different page types can be created with one template. I'm totally open to this.

I don't like the way that the site currently handles product images, nobody wants to click on even thumbnail to see the product. http://dalvosafeportals.com/products/personnel-doors/

Totally open to suggestions on layout to enable the feeling outlined in the brief above.

Please ask if anything is not clear or you need answers to drill down on specifics.

Sick

Target Market(s)

Businesses that buy steel doors

Font styles to use
Sans Serif
Other font styles liked:
• Copperplate Gothic Bold - For Company Name but we are open to suggestions

Colors

Designer to choose colors to be used in the design.

Requirements
Must have
• Professional looking, clean design
• Conveys strength, power and weight to represent the quality of the products, the characteristics of steel and the security that they provide.
• Incorporates black and yellow stripes of our branding
• Ability to create pages with content as seen at www.dalvosafeportals.com
• A better way of showing the product images
Nice to have
• If possible. a design that gives off the feeling that not only do we supply the products we also make them in house too. I don't know what this looks like but a way of differentiating between a supply only business and one that manufacturers the product too.
Should not have
• We don't like the current thumbnail method of showing the product images

```html
<!DOCTYPE html>
<html lang="en">
<head>
<meta charset="utf-8">
<title>Dalvesham Engineering Ltd – Steel Security Doors</title>
<link href="https://fonts.googleapis.com/css2?family=Maven+Pro:wght@400;500;600;700&display=swap" rel="stylesheet">
<style>
:root{
  --yellow:#f4ea00;
  --ink:#151515;
  --bg-dark:#1b1b1b;
  --bg-mid:#232323;
  --bg-card:#2b2b2b;
  --text:#ffffff;
  --muted:#d8d8d8;
  --white:#ffffff;
}
*{margin:0;padding:0;box-sizing:border-box}
html,body{width:1200px;height:3297px;overflow:hidden}
body{position:relative;background:var(--bg-dark);color:var(--text);font-family:"Maven Pro",Arial,sans-serif}
.abs{position:absolute}
a{color:inherit;text-decoration:none}

/* header */
.site-header{left:0;top:0;width:1200px;height:132px;background:var(--ink)}
.brand{left:110px;top:30px;display:flex;align-items:center;gap:14px}
.brand-mark{width:40px;height:66px;background:var(--yellow)}
.brand-name{font-size:29px;font-weight:700;color:var(--white);line-height:1.05;letter-spacing:1px;text-transform:uppercase}
.top-contact{right:110px;top:26px;display:flex;gap:34px;font-size:16px}
.top-contact span{display:flex;align-items:center;gap:9px}
.top-contact .phone{color:var(--yellow)}
.main-nav{right:110px;top:68px;display:flex;gap:28px;font-size:15px;font-weight:500}
.main-nav a{padding-bottom:9px}
.main-nav .active{color:var(--yellow);border-bottom:3px solid var(--yellow)}

/* hero */
.hero{left:0;top:132px;width:1200px;height:677px;background:linear-gradient(90deg,#8a7a72 0%,#d9d5cf 30%,#b46c4e 45%,#cfcac2 60%,#3c2d28 80%,#2a221f 100%)}
.hero-arrow{top:424px;width:32px;height:32px;border-radius:50%}
.hero-arrow.prev{left:50px;background:var(--white)}
.hero-arrow.next{right:50px;background:var(--yellow)}
.hero-dots{left:576px;top:836px;display:flex;gap:6px}
.hero-dots i{width:6px;height:6px;border-radius:50%;background:var(--white)}
.hero-dots i:first-child{background:var(--yellow)}

/* sections */
.section-title{width:1200px;left:0;text-align:center;font-size:35px;font-weight:500}
.section-sub{width:1200px;left:0;text-align:center;font-size:18px;font-weight:500}
.btn{display:flex;align-items:center;justify-content:center;background:var(--yellow);color:var(--ink);font-weight:600;font-size:15px;border-radius:16px;height:32px}

.tabs{left:0;width:1200px;top:952px;display:flex;justify-content:center;gap:0;font-size:14px}
.tabs span{padding:0 24px;border-left:1px solid #555}
.tabs span:first-child{border:none;color:var(--yellow);text-decoration:underline}
.tab-arrows{left:1040px;top:953px;display:flex;gap:6px}
.tab-arrows i{width:16px;height:16px;border-radius:50%;background:var(--white)}
.tab-arrows i+i{background:var(--yellow)}
.product-card{top:1020px;width:228px;height:290px;background:var(--bg-card)}
.product-card .photo{height:244px}
.product-card .name{text-align:center;font-size:15px;padding-top:14px}

.accessories{left:0;top:1442px;width:1200px;height:609px;background:var(--bg-mid)}
.intro{left:0;width:1200px;text-align:center;font-size:15px;color:var(--muted)}
.block-title{left:119px;font-size:19px;font-weight:500}
.copy{left:119px;font-size:14.5px;color:var(--muted);line-height:35px}
.bullets{left:145px;font-size:14.5px;color:var(--muted);line-height:17px;width:470px}
.bullets li{margin-bottom:0}

.downloads{left:0;top:2051px;width:1200px;height:602px;background:var(--bg-dark)}
.dl-links{left:119px;top:2230px;font-size:14.5px;color:var(--muted);line-height:35px}
.dl-list{left:145px;top:2342px;font-size:15px;line-height:27px;color:var(--white)}
.dl-list .first{color:var(--yellow);text-decoration:underline}

.newsletter{left:0;top:2653px;width:1200px;height:204px;background:#1f1f1f}
.news-form{left:341px;top:2780px;width:510px;height:31px;border-radius:16px;background:#3a3a3a;display:flex;overflow:hidden}
.news-form span{flex:1;padding:7px 20px;font-size:14px;color:var(--muted)}
.news-form b{width:130px;background:var(--yellow);color:var(--ink);font-size:14px;font-weight:500;display:flex;align-items:center;justify-content:center}

.site-footer{left:0;top:2857px;width:1200px;height:385px;background:linear-gradient(180deg,#181818,#242220 50%,#141414)}
.foot-title{top:2962px;font-size:17px;font-weight:500}
.foot-title::after{content:"";display:block;width:68px;height:2px;background:var(--white);margin-top:14px}
.foot-about{left:117px;top:3040px;width:265px;font-size:14px;line-height:19px}
.badges{left:119px;top:3116px;display:flex;gap:10px}
.badges i{width:72px;height:45px;background:#e7e7e7;border-radius:3px}
.foot-links{left:425px;top:3038px;font-size:14px;line-height:18.5px;list-style:disc}
.foot-address{left:631px;top:3040px;font-size:14px;line-height:22px}
.foot-address p{display:flex;gap:8px;align-items:flex-start}
.field{background:var(--white);color:#777;font-size:12px;padding:4px 8px}
.send{left:976px;top:3123px;width:103px;height:22px;border-radius:11px;background:var(--yellow);color:var(--ink);font-size:12px;display:flex;align-items:center;justify-content:center}

.legal-bar{left:0;top:3242px;width:1200px;height:55px;background:var(--white);color:var(--ink)}
.legal-bar p{position:absolute;left:120px;top:18px;font-size:14px;font-weight:500}
.socials{position:absolute;left:894px;top:14px;display:flex;gap:8px}
.socials i{width:27px;height:27px;border-radius:50%;background:var(--ink)}
</style>
</head>
<body>

<header class="abs site-header">
  <div class="abs brand"><span class="brand-mark"></span><span class="brand-name">Dalvesham<br>Engineering Ltd.</span></div>
  <div class="abs top-contact">
    <span><svg width="20" height="20" viewBox="0 0 20 20"><circle cx="10" cy="10" r="10" fill="#fff"/><rect x="5" y="6.5" width="10" height="7" fill="#151515"/><path d="M5 7l5 4 5-4" stroke="#fff" fill="none"/></svg>sales@dalvoportals.com</span>
    <span class="phone"><svg width="20" height="20" viewBox="0 0 20 20"><circle cx="10" cy="10" r="9" fill="none" stroke="#f4ea00" stroke-width="1.6"/><path d="M7 6c-1 1 0 4 2 6s5 3 6 2l-2-2-1 1c-1-.5-2.5-2-3-3l1-1z" fill="#f4ea00"/></svg>+44 (0)1632 960 418</span>
  </div>
  <nav class="abs main-nav">
    <a class="active">Home</a><a>Products ▾</a><a>Accessories ▾</a><a>Delivery &amp; Lead Times</a><a>Downloads</a><a>Contact</a>
  </nav>
</header>

<section class="abs hero" role="img" aria-label="Photo of a terraced townhouse with a red panelled front door, iron railings and a bicycle"></section>
<span class="abs hero-arrow prev"></span><span class="abs hero-arrow next"></span>
<div class="abs hero-dots"><i></i><i></i><i></i><i></i></div>

<h2 class="abs section-title" style="top:884px">Freature Product</h2>
<div class="abs tabs"><span>All</span><span>Personnel Doors</span><span>Fire Exit Doors</span><span>Blank Doors</span><span>Technical Videos</span><span>Accessories</span></div>
<div class="abs tab-arrows"><i></i><i></i></div>

<article class="abs product-card" style="left:116px"><div class="photo" role="img" aria-label="Grey steel door with lever handle and anti-vandal shroud" style="background:linear-gradient(135deg,#6f767d,#4d5358)"></div><p class="name">Anti-Vandal Shroud</p></article>
<article class="abs product-card" style="left:366px"><div class="photo" role="img" aria-label="Worker spray painting a steel door" style="background:linear-gradient(135deg,#8d9686,#c9ccc3 60%,#5f665c)"></div><p class="name">Paint Finish</p></article>
<article class="abs product-card" style="left:614px"><div class="photo" role="img" aria-label="Cloaking frame product render" style="background:linear-gradient(135deg,#ffffff,#e2e2e2)"></div><p class="name">Cloaking Frames</p></article>
<article class="abs product-card" style="left:857px"><div class="photo" role="img" aria-label="Blue steel door with hydraulic closer and vision panel" style="background:linear-gradient(135deg,#1f4e8c,#143663)"></div><p class="name">Hydraulic Closers</p></article>
<a class="abs btn" style="left:541px;top:1349px;width:129px">View More</a>

<section class="abs accessories"></section>
<h2 class="abs section-title" style="top:1493px">Accessories Leadtimes</h2>
<p class="abs section-sub" style="top:1550px">Delivery</p>
<p class="abs intro" style="top:1588px">We use a select range of haulage companies to deliver our products, they have a proven record of delivering safely and on time.</p>
<p class="abs intro" style="top:1623px">Please contact us for a delivery quotation – All of our delivery prices are quoted at cost.</p>
<p class="abs intro" style="top:1656px">Alternatively it is possible to arrange a collection from our premises.</p>
<h3 class="abs block-title" style="top:1718px">Lead Times</h3>
<div class="abs copy" style="top:1748px"><p>Please find approximate lead times below.</p><p>For precise up-to-date lead times please contact our sales team.</p></div>
<ul class="abs bullets" style="top:1834px">
  <li>Multi-locking or blank door finished in primer – 2 working days + delivery</li>
  <li>Anti-vandal shutters and glazing units – 2 working days + delivery</li>
  <li>Fire exit or blank door with hardware fitted – 1 week + delivery</li>
  <li>Any door with a spray paint finish – 2 weeks + delivery</li>
</ul>
<a class="abs btn" style="left:122px;top:1940px;width:131px">View More</a>
<div class="abs" role="img" aria-label="Illustration of an aircraft, delivery lorry and van with parcels around a globe" style="left:631px;top:1719px;width:384px;height:250px;background:linear-gradient(160deg,#f4f4f4,#c9c4bb 55%,#9c8a6e)"></div>

<section class="abs downloads"></section>
<h2 class="abs section-title" style="top:2108px">Downloads</h2>
<p class="abs section-sub" style="top:2160px">Brochures</p>
<div class="abs dl-links">
  <p>10-Point Locking Steel Personnel Doors Brochure (click to download) (1.67 MB bytes)</p>
  <p>Steel Fire Exit Doors Brochure (click to download) (1.53 MB bytes)</p>
  <p>Anti-Vandal Steel Shutters and Glazing Units Brochure (click to download) (1.9 MB bytes)</p>
</div>
<ul class="abs dl-list">
  <li class="first">Technical Diagrams - Doors - Overview</li>
  <li>Technical Diagrams - Doors - Frame Profile</li>
  <li>Technical Diagrams - Doors - Fixing Points</li>
  <li>Door Threshold Diagrams &nbsp;&nbsp;&nbsp;&nbsp;&nbsp;&nbsp;• &nbsp;Vision Panels</li>
  <li>Maintenance &nbsp;&nbsp;&nbsp;&nbsp;&nbsp;&nbsp;&nbsp;&nbsp;&nbsp;&nbsp;&nbsp;&nbsp;&nbsp;&nbsp;&nbsp;• &nbsp;Fitting Istructions</li>
</ul>
<a class="abs btn" style="left:122px;top:2498px;width:131px">View More</a>
<div class="abs" role="img" aria-label="Illustration of a PDF document icon" style="left:809px;top:2253px;width:261px;height:257px;background:linear-gradient(160deg,#ffffff 0%,#e6e6e6 70%,#c0392b 100%)"></div>

<section class="abs newsletter"></section>
<h2 class="abs section-title" style="top:2710px;font-size:24px">Join The Newletter</h2>
<p class="abs section-sub" style="top:2745px;font-size:14px;font-weight:400">Sign up for Our Newsletter</p>
<div class="abs news-form"><span>Email here</span><b>Subscribe</b></div>

<footer class="abs site-footer" role="img" aria-label="Darkened photo of the factory building behind the footer"></footer>
<div class="abs brand" style="top:2945px;left:114px"><span class="brand-mark" style="width:30px;height:60px"></span><span class="brand-name" style="font-size:24px">Dalvesham<br>Engineering Ltd.</span></div>
<p class="abs foot-about">Lorem Ipsum is simply dummy text the printing and ypesetting industry has been the industry's standard dummy...</p>
<div class="abs badges"><i></i><i></i><i style="background:#c7762c"></i></div>

<h4 class="abs foot-title" style="left:409px">Quick Link</h4>
<ul class="abs foot-links"><li>Home</li><li>Products</li><li>Accessories</li><li>Delivery &amp; Lead Times</li><li>Downloads</li><li>Contact</li></ul>

<h4 class="abs foot-title" style="left:631px">Address</h4>
<div class="abs foot-address">
  <p><svg width="12" height="16" viewBox="0 0 12 16"><path d="M6 0a6 6 0 0 0-6 6c0 4 6 10 6 10s6-6 6-10a6 6 0 0 0-6-6z" fill="#fff"/><circle cx="6" cy="6" r="2" fill="#222"/></svg><span>Harnley Rise, Oakwell,<br>Hull, HU99 4ZZ<br>Zip :00000</span></p>
  <p><svg width="12" height="14" viewBox="0 0 12 14"><path d="M2 1c-2 2 0 6 3 9s6 4 7 2l-2-2-1.5 1c-1-.5-3-2.5-3.5-3.5L6 6 4 3z" fill="#fff"/></svg>+44 (0)1632 960 418</p>
  <p><svg width="13" height="10" viewBox="0 0 13 10"><rect width="13" height="10" fill="#fff"/><path d="M0 0l6.5 5L13 0" stroke="#222" fill="none"/></svg>sales@dalvoportals.com</p>
</div>

<h4 class="abs foot-title" style="left:846px">Quick Contact</h4>
<div class="abs field" style="left:848px;top:3033px;width:112px;height:22px">Name</div>
<div class="abs field" style="left:969px;top:3033px;width:110px;height:22px">Phone</div>
<div class="abs field" style="left:848px;top:3064px;width:231px;height:48px">Message</div>
<a class="abs send">SEND</a>

<div class="abs legal-bar">
  <p>Privacy policy - Legal mentions - Terms and Conditions</p>
  <div class="socials"><i></i><i></i><i></i><i></i><i></i></div>
</div>

</body>
</html>
```